Harborline Auto LLC

Car Dealer Customer Service
Address: 2874 Cresthaven Road, Shelbyville, TN 37162
web: www.harborlineautoxq.net
email: harborlineautoxq@mailnest.example
Phone: (931) 555-0148
Phone: (629) 555-0173

```html
<!DOCTYPE html>
<html lang="en">
<head>
<meta charset="utf-8">
<title>Harborline Auto LLC – Business Card</title>
<link href="https://fonts.googleapis.com/css2?family=Montserrat:wght@500;600;800&display=swap" rel="stylesheet">
<style>
  :root {
    --ink-blue: #1a73ad;
    --gold: #ebb03f;
    --card-black: #141414;
    --card-white: #ffffff;
    --text-gray: #555a60;
    --backdrop: #d9d9d9;
  }
  * { margin: 0; padding: 0; box-sizing: border-box; }
  html, body { width: 1200px; height: 900px; overflow: hidden; }
  body {
    background: var(--backdrop);
    font-family: "Montserrat", Arial, sans-serif;
    position: relative;
  }
  .card {
    position: absolute;
    left: 250px;
    width: 700px;
    height: 400px;
    box-shadow: 0 6px 18px rgba(0,0,0,.25);
    overflow: hidden;
  }
  .card-back { top: 35px; background: var(--card-black); }
  .card-front { top: 465px; background: var(--card-white); }

  .brand-mark {
    position: absolute;
    display: flex;
    align-items: center;
    font-weight: 800;
    color: var(--ink-blue);
    text-transform: uppercase;
    letter-spacing: .5px;
    white-space: nowrap;
  }
  .brand-dot {
    border-radius: 50%;
    background: var(--gold);
    flex: none;
  }
  .card-back .brand-mark {
    left: 0; right: 0; top: 180px;
    justify-content: center;
    gap: 14px;
    font-size: 30px;
    color: var(--gold);
  }
  .card-back .brand-dot { width: 30px; height: 30px; }

  .card-front .brand-mark {
    left: 30px; top: 120px;
    width: 280px;
    flex-direction: column;
    gap: 16px;
    font-size: 24px;
  }
  .card-front .brand-dot { width: 64px; height: 64px; }

  .divider {
    position: absolute;
    left: 338px; top: 100px;
    width: 2px; height: 165px;
    background: var(--ink-blue);
  }
  .contact {
    position: absolute;
    left: 362px; top: 100px;
    color: var(--text-gray);
    font-weight: 500;
    font-size: 14px;
    line-height: 1.45;
  }
  .contact .role {
    color: var(--ink-blue);
    font-weight: 600;
    font-size: 16px;
  }
  .contact .address { margin-bottom: 10px; }
  .contact-line { display: flex; align-items: center; gap: 8px; }
  .contact-line svg { width: 13px; height: 13px; flex: none; }

  .bands { position: absolute; left: 0; top: 0; }
  .web {
    position: absolute;
    left: 478px; top: 352px;
    width: 222px;
    height: 48px;
    display: flex;
    align-items: center;
    justify-content: center;
    color: #fff;
    font-weight: 500;
    font-size: 14px;
  }
</style>
</head>
<body>

<section class="card card-back" aria-label="Card back">
  <div class="brand-mark"><span class="brand-dot"></span>Harborline Auto</div>
</section>

<section class="card card-front" aria-label="Card front">
  <svg class="bands" width="700" height="400" viewBox="0 0 700 400" aria-hidden="true">
    <rect x="0" y="389" width="480" height="11" fill="var(--gold)"/>
    <polygon points="470,346 700,346 700,400 478,400" fill="var(--ink-blue)"/>
  </svg>

  <div class="brand-mark"><span class="brand-dot"></span>Harborline Auto</div>

  <div class="divider"></div>

  <div class="contact">
    <div class="role">Car Dealer Customer Service</div>
    <div class="address">2874 Cresthaven Road<br>Shelbyville, TN 37162</div>
    <div class="contact-line">
      <svg viewBox="0 0 24 24"><path fill="var(--gold)" d="M6.6 10.8a15.1 15.1 0 0 0 6.6 6.6l2.2-2.2a1 1 0 0 1 1-.25 11.4 11.4 0 0 0 3.6.57 1 1 0 0 1 1 1V20a1 1 0 0 1-1 1A17 17 0 0 1 3 4a1 1 0 0 1 1-1h3.5a1 1 0 0 1 1 1c0 1.25.2 2.45.57 3.57a1 1 0 0 1-.25 1z"/></svg>
      (931) 555-0148
    </div>
    <div class="contact-line">
      <svg viewBox="0 0 24 24"><path fill="var(--gold)" d="M6.6 10.8a15.1 15.1 0 0 0 6.6 6.6l2.2-2.2a1 1 0 0 1 1-.25 11.4 11.4 0 0 0 3.6.57 1 1 0 0 1 1 1V20a1 1 0 0 1-1 1A17 17 0 0 1 3 4a1 1 0 0 1 1-1h3.5a1 1 0 0 1 1 1c0 1.25.2 2.45.57 3.57a1 1 0 0 1-.25 1z"/></svg>
      (629) 555-0173
    </div>
    <div class="contact-line">
      <svg viewBox="0 0 24 24"><path fill="var(--gold)" d="M2 5h20v14H2z"/><path fill="none" stroke="#fff" stroke-width="1.8" d="M2 5l10 8 10-8"/></svg>
      harborlineautoxq@mailnest.example
    </div>
  </div>

  <div class="web">www.harborlineautoxq.net</div>
</section>

</body>
</html>
```